Modern Attractive Letterhead for Veterinary House Call Business.

A letterhead which can be printed on A4, A5 and A6 paper sizes.
To have: ( our files to be uploaded)
1. Logo with Text
2. telephone
3. email
4. website
5. Address

Target Market(s)

60-85year mainly women pet owners. Also market include families, young professionals, busy people who have dogs and cats

Industry/Entity Type

Business

Requirements
Must have
• 1. Logo with Text ( provided)
• 2. telephone
• 3. email
• 4. website
• 5. Address
Nice to have
• Needs to be modern, preferably warm and caring in nature( if possible )
Should not have
• difficulty in printing A5 and A6

```html
<!DOCTYPE html>
<html lang="en">
<head>
<meta charset="utf-8">
<title>Hearthside Vet Care – Letterhead</title>
<link rel="stylesheet" href="https://fonts.googleapis.com/css2?family=Cinzel:wght@400;600&display=swap">
<style>
  :root {
    --paper: #ffffff;
    --ink: #2b2b2b;
    --brand-green: #5cbf2a;
    --brand-blue-deep: #1c58b0;
    --brand-blue-bright: #14b3ef;
    --rule: #8a8a8a;
    --icon-blue: #1f6fc7;
    --footer-text: #eaf6ff;
  }
  html, body {
    margin: 0;
    padding: 0;
    width: 953px;
    height: 1200px;
    overflow: hidden;
    background: var(--paper);
  }
  .letterhead {
    position: relative;
    width: 953px;
    height: 1200px;
    background: var(--paper);
    font-family: "Cinzel", serif;
    color: var(--ink);
    overflow: hidden;
  }
  .brand {
    position: absolute;
    left: 30px;
    top: 62px;
    display: flex;
    align-items: center;
    gap: 14px;
  }
  .brand-dot {
    width: 34px;
    height: 34px;
    border-radius: 50%;
    background: var(--brand-blue-deep);
  }
  .brand-name {
    margin: 0;
    font-family: "Cinzel", serif;
    font-weight: 600;
    font-size: 36px;
    letter-spacing: 0.5px;
    color: var(--brand-green);
  }
  .contact {
    position: absolute;
    left: 596px;
    top: 44px;
    padding: 0 0 0 14px;
    border-left: 1.5px solid var(--rule);
    list-style: none;
    margin: 0;
  }
  .contact-item {
    display: flex;
    align-items: center;
    gap: 10px;
    height: 30px;
    font-size: 16px;
    white-space: nowrap;
    color: var(--ink);
  }
  .contact-icon {
    width: 18px;
    height: 18px;
    flex: none;
  }
  .footer-waves {
    position: absolute;
    left: 0;
    top: 0;
    width: 953px;
    height: 1200px;
  }
  .postal-address {
    position: absolute;
    left: 650px;
    top: 1128px;
    margin: 0;
    font-style: normal;
    font-size: 19px;
    line-height: 26px;
    white-space: nowrap;
    color: var(--footer-text);
  }
</style>
</head>
<body>
<main class="letterhead">
  <svg class="footer-waves" viewBox="0 0 735 950" preserveAspectRatio="none" aria-hidden="true">
    <defs>
      <linearGradient id="wave-blue" x1="0" y1="0" x2="1" y2="0">
        <stop offset="0" style="stop-color:#1c58b0"/>
        <stop offset="1" style="stop-color:#14b3ef"/>
      </linearGradient>
    </defs>
    <path d="M0 906 C150 902 300 882 420 862 C540 842 640 838 735 837 L735 848 C620 850 520 860 420 874 C300 892 150 916 0 917 Z" fill="#5cbf2a"/>
    <path d="M0 924 C180 918 320 893 440 873 C560 855 650 856 735 854 L735 950 L0 950 Z" fill="url(#wave-blue)"/>
    <path d="M0 940 C200 934 340 906 470 886 C580 870 660 866 735 866" fill="none" stroke="#ffffff" stroke-width="1.4" opacity="0.9"/>
  </svg>

  <header class="brand">
    <span class="brand-dot"></span>
    <h1 class="brand-name">Hearthside Vet Care</h1>
  </header>

  <ul class="contact">
    <li class="contact-item">
      <svg class="contact-icon" viewBox="0 0 20 20" aria-hidden="true">
        <circle cx="10" cy="10" r="8.5" fill="none" stroke="var(--icon-blue)" stroke-width="1.6"/>
        <path d="M7 5.5 L9 8 L8 9.5 C8.8 11 9.5 11.8 11 12.5 L12.5 11.5 L14.5 13.5 L13 15 C10 14.5 6 10.5 5.5 7.5 Z" fill="var(--icon-blue)"/>
      </svg>
      0400 512 839
    </li>
    <li class="contact-item">
      <svg class="contact-icon" viewBox="0 0 20 20" aria-hidden="true">
        <rect x="2" y="5" width="16" height="11" fill="var(--icon-blue)"/>
        <path d="M2 5 L10 11 L18 5" fill="none" stroke="#ffffff" stroke-width="1.3"/>
      </svg>
      hello@hearthsidevet.com.au
    </li>
    <li class="contact-item">
      <svg class="contact-icon" viewBox="0 0 20 20" aria-hidden="true">
        <g fill="none" stroke="var(--icon-blue)" stroke-width="1.3">
          <circle cx="10" cy="10" r="8"/>
          <ellipse cx="10" cy="10" rx="3.5" ry="8"/>
          <path d="M2 10 H18 M3.5 6 H16.5 M3.5 14 H16.5"/>
        </g>
      </svg>
      www.hearthsidevet.com.au
    </li>
  </ul>

  <address class="postal-address">
    PO Box 2210<br>
    Riverbend Qld 4070
  </address>
</main>
</body>
</html>
```